Zia Dorvelli's Crostalines

Looking for a packaging Label for Italian cookies. It has started with my great grandmothers Pizzelle recipe. Recipe has been in the family for over 100 years.
The packaging will be either clear plastic bags or Clear plastic hinged containers. Hoping for something elegant but traditional Italian. I have attached the company logo for color and idea possibilities
Would also like to give donation to helping animal foundations

Target Market(s)

Cookie lovers, coffee and tea drinkers, lighter alternative to heavy cookies

Requirements
Nice to have
• Family, Italian tradition

```html
<!DOCTYPE html>
<html lang="en">
<head>
<meta charset="utf-8">
<title>Zia Dorvelli's Pizzelle Label – Vanilla</title>
<link href="https://fonts.googleapis.com/css2?family=Old+Standard+TT:wght@400;700&family=Playball&family=Libre+Caslon+Text:wght@400;700&display=swap" rel="stylesheet">
<style>
  :root {
    --backdrop: #c39a6d;
    --rim-brown: #7b4e25;
    --rim-orange: #f39a1e;
    --label-dark: #2d3834;
    --gold-text: #c7a272;
    --shield-white: #ffffff;
    --brand-orange: #e8692a;
    --title-red: #c8202a;
    --flavour-blue: #25a8df;
    --weight-red: #cf1f2b;
    --flag-green: #009246;
    --flag-red: #ce2b37;
    --cookie-light: #f0a445;
    --cookie-deep: #c9641a;
  }
  html, body {
    margin: 0;
    padding: 0;
    width: 1200px;
    height: 1200px;
    overflow: hidden;
    background: var(--backdrop);
  }
  .label-canvas {
    display: block;
    width: 1200px;
    height: 1200px;
  }
  .title-main {
    font-family: "Old Standard TT", "Libre Caslon Text", serif;
    font-weight: 700;
    font-size: 192px;
  }
  .title-script {
    font-family: "Playball", cursive;
    font-size: 112px;
    fill: var(--rim-orange);
  }
  .brand-name {
    font-family: "Libre Caslon Text", serif;
    font-weight: 400;
    font-size: 50px;
    fill: var(--brand-orange);
  }
  .seal-text {
    font-family: "Libre Caslon Text", serif;
    font-size: 21px;
    letter-spacing: 3px;
    fill: var(--gold-text);
  }
  .seal-number {
    font-family: "Libre Caslon Text", serif;
    font-weight: 700;
    font-size: 56px;
    fill: var(--gold-text);
  }
  .origin-note {
    font-family: "Libre Caslon Text", serif;
    font-size: 32px;
    letter-spacing: 1px;
    fill: var(--gold-text);
  }
  .flavour-name {
    font-family: "Libre Caslon Text", serif;
    font-size: 94px;
    fill: #ffffff;
  }
  .weight-text {
    font-family: "Libre Caslon Text", serif;
    font-size: 40px;
    fill: #ffffff;
  }
</style>
</head>
<body>
<svg class="label-canvas" viewBox="0 0 1932 1932" xmlns="http://www.w3.org/2000/svg">
  <defs>
    <clipPath id="label-face">
      <ellipse cx="977" cy="990" rx="543" ry="653"/>
    </clipPath>
    <radialGradient id="cookie-tone" cx="50%" cy="45%" r="55%">
      <stop offset="0%" stop-color="var(--cookie-deep)"/>
      <stop offset="70%" stop-color="#e08a2e"/>
      <stop offset="100%" stop-color="var(--cookie-light)"/>
    </radialGradient>
    <path id="seal-arc-top" d="M 512 710 A 84 84 0 0 1 680 710"/>
    <path id="seal-arc-bottom" d="M 499 710 A 97 97 0 0 0 693 710"/>
  </defs>

  <!-- oval frame -->
  <g class="oval-frame">
    <ellipse cx="977" cy="992" rx="582" ry="692" fill="var(--rim-brown)"/>
    <ellipse cx="977" cy="990" rx="562" ry="672" fill="var(--rim-orange)"/>
    <ellipse cx="977" cy="990" rx="548" ry="658" fill="var(--rim-brown)"/>
    <ellipse cx="977" cy="990" rx="543" ry="653" fill="var(--label-dark)"/>
  </g>

  <!-- cookie area -->
  <g class="cookie-area" clip-path="url(#label-face)">
    <circle cx="978" cy="1495" r="345" fill="url(#cookie-tone)" role="img" aria-label="Golden vanilla pizzelle waffle cookie with pressed snowflake pattern"/>
    <rect class="flavour-band" x="400" y="1315" width="1160" height="97" fill="var(--flavour-blue)"/>
  </g>
  <text class="flavour-name" x="968" y="1396" text-anchor="middle">Vanilla</text>

  <!-- net weight tag -->
  <g class="weight-tag">
    <rect x="775" y="1455" width="380" height="160" fill="var(--weight-red)"/>
    <text class="weight-text" x="965" y="1522" text-anchor="middle">NET WT.</text>
    <text class="weight-text" x="965" y="1585" text-anchor="middle">7oz (200g)</text>
  </g>

  <!-- brand shield -->
  <g class="brand-shield">
    <path d="M 730 305 L 1205 305 L 1205 760 Q 1205 790 1175 790 L 1050 790 Q 1010 790 990 840 Q 970 790 930 790 L 760 790 Q 730 790 730 760 Z" fill="var(--rim-orange)"/>
    <path d="M 748 310 L 1187 310 L 1187 752 Q 1187 772 1167 772 L 1045 772 Q 1008 772 990 815 Q 972 772 935 772 L 768 772 Q 748 772 748 752 Z" fill="var(--shield-white)"/>
    <circle cx="968" cy="490" r="42" fill="var(--brand-orange)"/>
    <text class="brand-name" x="968" y="640" text-anchor="middle">Zia Dorvelli's</text>
  </g>

  <!-- heritage seal -->
  <g class="heritage-seal">
    <circle cx="596" cy="710" r="112" fill="none" stroke="var(--gold-text)" stroke-width="3"/>
    <circle cx="596" cy="710" r="66" fill="none" stroke="var(--gold-text)" stroke-width="3"/>
    <circle cx="506" cy="710" r="3" fill="var(--gold-text)"/>
    <circle cx="686" cy="710" r="3" fill="var(--gold-text)"/>
    <text class="seal-text"><textPath href="#seal-arc-top" startOffset="50%" text-anchor="middle" transform="translate(6 0)">FAMILY RECIPE</textPath></text>
    <text class="seal-text"><textPath href="#seal-arc-bottom" startOffset="50%" text-anchor="middle">YEARS OLD</textPath></text>
    <text class="seal-number" x="596" y="730" text-anchor="middle">100</text>
  </g>

  <!-- origin mark -->
  <g class="origin-mark">
    <path d="M 1278 410 L 1318 422 L 1318 645 L 1278 645 Z" fill="var(--flag-green)"/>
    <path d="M 1318 422 L 1360 434 L 1360 645 L 1318 645 Z" fill="#ffffff"/>
    <path d="M 1360 434 L 1400 446 L 1400 645 L 1360 645 Z" fill="var(--flag-red)"/>
    <text class="origin-note" x="1338" y="692" text-anchor="middle">AUTHENTIC</text>
    <text class="origin-note" x="1338" y="735" text-anchor="middle">ITALIAN</text>
  </g>

  <!-- product title -->
  <text class="title-main" x="484" y="1002" textLength="945" lengthAdjust="spacingAndGlyphs" fill="var(--title-red)">PIZZELLE</text>
  <text class="title-main" x="495" y="1012" textLength="945" lengthAdjust="spacingAndGlyphs" fill="#ffffff">PIZZELLE</text>
  <text class="title-script" x="510" y="1108" textLength="910" lengthAdjust="spacingAndGlyphs">Italian waffle cookies</text>
</svg>
</body>
</html>
```